I need a fresh looking, exciting and loaded design for Full service Restaurant

We need a web design for our restaurant, which offers full service Pakistani and Indian food in PA, USA. Design should be elegant, simplified so customers can navigate easily and order food online for catering as well as delivery. We need loads of pictures and room to grow. I already have a web address via vemrilo.com. It should include SSL and e-commerce for ordering food.
Be original and be creative and make it a fun site :)

```html
<!DOCTYPE html>
<html lang="en">
<head>
<meta charset="utf-8">
<title>Saffron Lane – Pakistani &amp; Indian Cuisine</title>
<link rel="stylesheet" href="https://fonts.googleapis.com/css2?family=Open+Sans:ital,wght@0,400;0,600;0,700;1,400&family=Great+Vibes&display=swap">
<style>
:root{
  --red:#d8201f;
  --red-dark:#b3110f;
  --red-deep:#8f0d0c;
  --green:#2a5d10;
  --green-dark:#1f4a0a;
  --cream:#f7efdc;
  --cream-dark:#efe2c4;
  --ink:#3a3a3a;
  --muted:#555;
  --charcoal:#1d1d1d;
  --star:#f29a16;
  --lime:#b6e03a;
  --white:#fff;
}
*{box-sizing:border-box;margin:0;padding:0}
html,body{width:1200px;height:2384px;overflow:hidden}
body{font-family:"Open Sans",Arial,sans-serif;color:var(--ink);background:var(--cream)}
.canvas{position:relative;width:1200px;height:2384px;overflow:hidden}
.abs{position:absolute}

/* hero */
.hero{left:0;top:0;width:1200px;height:652px;
  background:radial-gradient(ellipse at 30% 45%,#e8352f 0%,var(--red) 45%,var(--red-dark) 100%);
  border-top:5px solid var(--green-dark)}
.brand{left:84px;top:40px;display:flex;align-items:center;gap:12px}
.brand-dot{width:46px;height:46px;border-radius:50%;background:var(--white)}
.brand-name{font-size:34px;font-weight:700;color:var(--white);letter-spacing:.5px}
.nav{left:378px;top:56px;width:742px;height:47px;background:#f6f3ee;border-radius:4px;
  display:flex;align-items:center;justify-content:space-evenly;padding:0 30px}
.nav a{font-size:13px;font-weight:600;color:#333;text-decoration:none;letter-spacing:.3px}
.nav .sep{width:1px;height:14px;background:#999}
.hero-title{left:84px;top:224px;font-family:"Great Vibes",cursive;font-size:92px;font-weight:400;color:var(--white);line-height:1}
.hero-sub{left:86px;top:340px;width:500px;font-size:18px;line-height:26px;color:#49a02a;font-weight:600;text-transform:uppercase}
.hero-text{left:86px;top:408px;width:490px;font-size:12px;line-height:24px;color:var(--white);font-style:italic}
.btn-more{left:87px;top:505px;width:188px;height:50px;border-radius:25px;background:var(--green-dark);
  border:2px solid #e8e0c8;color:var(--white);font-size:15px;font-weight:400;display:flex;align-items:center;justify-content:center}
.dots{left:86px;top:612px;display:flex;gap:4px}
.dots span{width:14px;height:14px;border-radius:50%;border:2px solid var(--white)}
.dots span.on{background:var(--green-dark);border-color:var(--green-dark)}
.hero-photo{left:612px;top:205px;width:506px;height:410px;border-radius:50%;border:8px solid var(--red-deep);
  background:radial-gradient(ellipse at 50% 55%,#b07a4a 0%,#8a5a35 35%,#e9e4dc 75%,#ffffff 100%)}

/* zigzag edges */
.zig-down{height:14px;width:1200px;
  background:linear-gradient(135deg,var(--red-dark) 50%,transparent 50%) 0 0/12px 14px,
             linear-gradient(-135deg,var(--red-dark) 50%,transparent 50%) 0 0/12px 14px}
.zig-dark-top{height:12px;width:1200px;
  background:linear-gradient(45deg,transparent 50%,var(--charcoal) 50%) 0 0/12px 12px,
             linear-gradient(-45deg,transparent 50%,var(--charcoal) 50%) 0 0/12px 12px}
.zig-dark-bottom{height:12px;width:1200px;
  background:linear-gradient(135deg,var(--charcoal) 50%,transparent 50%) 0 0/12px 12px,
             linear-gradient(-135deg,var(--charcoal) 50%,transparent 50%) 0 0/12px 12px}
.zig-red-top{height:12px;width:1200px;
  background:linear-gradient(45deg,transparent 50%,var(--red) 50%) 0 0/12px 12px,
             linear-gradient(-45deg,transparent 50%,var(--red) 50%) 0 0/12px 12px}

/* welcome */
.welcome{left:0;top:652px;width:1200px;height:470px;
  background:radial-gradient(ellipse at 50% 50%,#fbf5e8 0%,var(--cream) 60%,var(--cream-dark) 100%)}
.section-title{font-size:24px;font-weight:700;color:var(--green);letter-spacing:.3px;display:flex;align-items:center;gap:10px}
.section-title em{font-style:normal;color:var(--red)}
.chili{width:26px;height:36px;border-radius:0 0 50% 50%;background:var(--red)}
.welcome-title{left:0;width:1200px;top:700px;justify-content:center}
.welcome-text{left:0;width:1200px;top:752px;text-align:center;font-size:12.5px;line-height:24px;color:var(--muted)}
.feature{width:320px;text-align:center}
.feature-icon{width:140px;height:140px;border-radius:50%;margin:0 auto;border:4px solid #f3ead5;box-shadow:0 2px 6px rgba(0,0,0,.25);
  display:flex;align-items:center;justify-content:center}
.feature-icon svg{width:76px;height:76px}
.feature-icon.green{background:var(--green-dark)}
.feature-icon.red{background:var(--red)}
.feature h3{margin-top:26px;font-size:14px;font-weight:600;color:#333}
.feature p{margin-top:6px;font-size:12px;line-height:24.5px;color:var(--muted)}

/* quote */
.quote{left:0;top:1120px;width:1200px;height:421px;background:radial-gradient(ellipse at 25% 40%,#3a3a3a 0%,#262626 50%,var(--charcoal) 100%)}
.quote-photo{left:700px;top:1120px;width:500px;height:421px;
  background:linear-gradient(120deg,#2a2a2a 0%,#5b3a2a 30%,#b84a2a 55%,#d9d2c6 70%,#4f6b2a 85%,#2a2a2a 100%)}
.quote-title{left:96px;top:1168px;font-size:24px;font-weight:700;color:var(--white)}
.field{height:38px;border:1px solid #bdbdbd;background:rgba(0,0,0,.25);color:var(--white);
  font-size:12px;padding:0 14px;display:flex;align-items:center;justify-content:space-between}
.caret{width:0;height:0;border-left:6px solid transparent;border-right:6px solid transparent;border-top:6px solid var(--white)}
.cal{width:12px;height:11px;border:2px solid #ddd;border-top-width:4px}
.field.msg{align-items:flex-start;padding-top:10px;height:61px}
.btn-book{left:98px;top:1465px;width:167px;height:41px;background:var(--red);color:var(--white);
  font-size:16px;font-weight:600;display:flex;align-items:center;justify-content:center}

/* services */
.services{left:0;top:1541px;width:1200px;height:628px;
  background:radial-gradient(ellipse at 50% 40%,#fbf5e8 0%,var(--cream) 60%,var(--cream-dark) 100%)}
.services-title{left:84px;top:1585px}
.services-text{left:84px;width:282px;font-size:12px;line-height:24.4px;color:var(--muted);text-align:justify}
.pager{left:87px;top:1958px;display:flex;gap:4px}
.pager span{width:26px;height:24px;background:#e4dccb;border:1px solid #cfc6b2;display:flex;align-items:center;justify-content:center;color:#888;font-size:13px}
.card{width:229px;height:236px;background:var(--white);box-shadow:0 1px 3px rgba(0,0,0,.18)}
.card-photo{height:183px}
.card-foot{height:53px;display:flex;align-items:center;justify-content:space-between;padding:0 10px}
.card-name{font-size:12px;color:#333}
.stars{font-size:11px;color:var(--star);letter-spacing:-.5px}
.stars b{color:#555;font-weight:400}

/* footer */
.footer{left:0;top:2169px;width:1200px;height:215px;background:radial-gradient(ellipse at 50% 40%,#e02723 0%,var(--red) 50%,var(--red-dark) 100%)}
.social{left:92px;top:2229px;display:flex;gap:8px}
.social span{width:38px;height:38px;border-radius:50%;border:2px solid var(--white);display:flex;align-items:center;justify-content:center}
.social span::after{content:"";width:10px;height:10px;border-radius:50%;background:var(--white)}
.copy{left:90px;top:2286px;font-size:12px;line-height:21px;color:var(--white)}
.tweets-title{left:413px;top:2219px;font-size:16px;font-weight:600;color:var(--white)}
.tweet{left:413px;top:2249px;width:270px;font-size:12px;line-height:22px;color:var(--white)}
.tweet .lead{padding-left:110px}
.tweet .time{color:var(--lime)}
.links{list-style:none;font-size:12px;line-height:24px;color:var(--white)}
.links li::before{content:"";display:inline-block;width:5px;height:5px;border-radius:50%;background:var(--white);margin-right:10px;vertical-align:middle}
</style>
</head>
<body>
<div class="canvas">

  <!-- hero -->
  <section class="abs hero"></section>
  <div class="abs brand"><span class="brand-dot"></span><span class="brand-name">Saffron Lane</span></div>
  <nav class="abs nav">
    <a href="#">HOME</a><span class="sep"></span>
    <a href="#">ABOUT US</a><span class="sep"></span>
    <a href="#">SERVICES</a><span class="sep"></span>
    <a href="#">PRODUCTS</a><span class="sep"></span>
    <a href="#">GALLERY</a><span class="sep"></span>
    <a href="#">CONTACT US</a>
  </nav>
  <h1 class="abs hero-title">Saffron Lane</h1>
  <p class="abs hero-sub">We offer full service Pakistani &amp; Indian food in Philadelphia, USA</p>
  <p class="abs hero-text">It is a long established fact that a reader will be distracted by the readable content of a page when looking at its layout. The point of using Lorem Ipsum is that it has a more-or-less normal distribution of letters, as opposed tmaking it look like readable English.</p>
  <div class="abs btn-more">READ MORE INFO</div>
  <div class="abs dots"><span></span><span></span><span class="on"></span><span></span><span></span></div>
  <div class="abs hero-photo" role="img" aria-label="Jars and bowls of whole spices, chillies, star anise and cinnamon"></div>

  <!-- welcome -->
  <section class="abs welcome"></section>
  <div class="abs zig-down" style="left:0;top:652px"></div>
  <h2 class="abs section-title welcome-title"><span class="chili" role="img" aria-label="Chilli ornament"></span>WELCOME TO <em>SAFFRON LANE</em></h2>
  <p class="abs welcome-text">It is a long established fact that a reader will be distracted by the readable content of a page when looking at its layout.<br>The point of using Lorem Ipsum is that it has a more-ormaking it look like readable English.</p>

  <div class="abs feature" style="left:91px;top:823px">
    <div class="feature-icon green">
      <svg viewBox="0 0 80 80" role="img" aria-label="Mortar and pestle icon">
        <rect x="40" y="8" width="10" height="36" rx="5" fill="#fff" transform="rotate(30 45 26)"/>
        <path d="M10 40 H70 A30 26 0 0 1 10 40 Z" fill="#fff"/>
        <rect x="28" y="64" width="24" height="6" rx="2" fill="#fff"/>
      </svg>
    </div>
    <h3>CONTRARY TO POPULAR</h3>
    <p>It is a long established fact that a reader will be distracted by the readable content of a page has making it look like readable English.</p>
  </div>
  <div class="abs feature" style="left:444px;top:823px">
    <div class="feature-icon red">
      <svg viewBox="0 0 80 80" role="img" aria-label="Chilli pepper icon">
        <path d="M30 18 C52 20 58 40 50 56 C44 68 28 72 14 70 C30 64 40 54 38 40 C37 32 33 24 30 18 Z" fill="#fff"/>
        <path d="M30 18 C32 12 38 8 44 8" stroke="#fff" stroke-width="4" fill="none" stroke-linecap="round"/>
      </svg>
    </div>
    <h3>CONTRARY TO POPULAR</h3>
    <p>It is a long established fact that a reader will be distracted by the readable content of a page has making it look like readable English.</p>
  </div>
  <div class="abs feature" style="left:797px;top:823px">
    <div class="feature-icon green">
      <svg viewBox="0 0 80 80" role="img" aria-label="Chef hat and spoon icon">
        <circle cx="28" cy="24" r="10" fill="#fff"/><circle cx="40" cy="18" r="11" fill="#fff"/><circle cx="52" cy="24" r="10" fill="#fff"/>
        <rect x="24" y="24" width="32" height="20" rx="2" fill="#fff"/>
        <rect x="22" y="56" width="30" height="5" rx="2.5" fill="#fff"/>
        <ellipse cx="58" cy="58.5" rx="9" ry="6" fill="#fff"/>
      </svg>
    </div>
    <h3>CONTRARY TO POPULAR</h3>
    <p>It is a long established fact that a reader will be distracted by the readable content of a page has making it look like readable English.</p>
  </div>

  <!-- request a quote -->
  <section class="abs quote"></section>
  <div class="abs quote-photo" role="img" aria-label="Chillies, garlic, basil, carrots, asparagus and a wooden spoon on a dark slate"></div>
  <div class="abs zig-dark-top" style="left:0;top:1108px"></div>
  <h2 class="abs quote-title">REQUEST A QUOTE</h2>
  <div class="abs field" style="left:98px;top:1233px;width:253px">Name :</div>
  <div class="abs field" style="left:372px;top:1233px;width:254px">Email :</div>
  <div class="abs field" style="left:98px;top:1285px;width:253px">Reservation Date :<span class="cal"></span></div>
  <div class="abs field" style="left:372px;top:1285px;width:254px">Time :<span class="caret"></span></div>
  <div class="abs field" style="left:98px;top:1336px;width:253px">People :<span class="caret"></span></div>
  <div class="abs field" style="left:372px;top:1336px;width:254px">Time :<span class="caret"></span></div>
  <div class="abs field msg" style="left:98px;top:1387px;width:528px">Message :</div>
  <div class="abs btn-book">BOOKING NOW</div>

  <!-- services -->
  <section class="abs services"></section>
  <div class="abs zig-dark-bottom" style="left:0;top:1541px"></div>
  <h2 class="abs section-title services-title"><span class="chili" role="img" aria-label="Chilli ornament"></span>OUR <em>SERVICES</em></h2>
  <p class="abs services-text" style="top:1645px">It is a long established fact that a reader will be distracted by the readable content of a page when looking at its layout. The point of using Lorem Ipsum is that it has a more-or-less normal distribution of letters, as opposed to using 'Content here, content here', making it look like readable English.</p>
  <p class="abs services-text" style="top:1839px">Many desktop publishing packages and web page editors now use Lorem Ipsum as their default model text, and a search for 'lorem ipsum' will uncover many web sites still in their infancy</p>
  <div class="abs pager" style="top:1958px"><span>&#8249;</span><span>&#8250;</span></div>

  <div class="abs card" style="left:397px;top:1592px"><div class="card-photo" role="img" aria-label="Grilled kebabs with salad" style="background:linear-gradient(160deg,#e9dcc4,#8a3f1c 45%,#5a2410 75%,#c9c2b6)"></div><div class="card-foot"><span class="card-name">PRODUCTS NAME</span><span class="stars">★★★★<b>☆</b></span></div></div>
  <div class="abs card" style="left:640px;top:1592px"><div class="card-photo" role="img" aria-label="Curries and saffron rice in bowls" style="background:linear-gradient(160deg,#c9b07a,#e07a22 45%,#b8401a 75%,#6a4a2a)"></div><div class="card-foot"><span class="card-name">PRODUCTS NAME</span><span class="stars">★★★★<b>☆</b></span></div></div>
  <div class="abs card" style="left:885px;top:1592px"><div class="card-photo" role="img" aria-label="Chickpea curry in a metal bowl" style="background:linear-gradient(160deg,#e8b060,#c07028 45%,#7a4a28 75%,#4a3a30)"></div><div class="card-foot"><span class="card-name">PRODUCTS NAME</span><span class="stars">★★★★<b>☆</b></span></div></div>
  <div class="abs card" style="left:397px;top:1850px"><div class="card-photo" role="img" aria-label="Chicken biryani in a serving dish" style="background:linear-gradient(160deg,#e8c070,#d88a30 45%,#b0521c 75%,#5a3a22)"></div><div class="card-foot"><span class="card-name">PRODUCTS NAME</span><span class="stars">★★★★<b>☆</b></span></div></div>
  <div class="abs card" style="left:640px;top:1850px"><div class="card-photo" role="img" aria-label="Braised lamb curry" style="background:linear-gradient(160deg,#6a3a22,#9a4a24 45%,#5a2a16 75%,#3a2014)"></div><div class="card-foot"><span class="card-name">PRODUCTS NAME</span><span class="stars">★★★★<b>☆</b></span></div></div>
  <div class="abs card" style="left:885px;top:1850px"><div class="card-photo" role="img" aria-label="Butter chicken in a black pan" style="background:linear-gradient(160deg,#2a2a2a,#c8401a 40%,#e0601e 65%,#2a2a2a)"></div><div class="card-foot"><span class="card-name">PRODUCTS NAME</span><span class="stars">★★★★<b>☆</b></span></div></div>

  <!-- footer -->
  <footer class="abs footer"></footer>
  <div class="abs zig-red-top" style="left:0;top:2158px"></div>
  <div class="abs social" role="img" aria-label="Social network links"><span></span><span></span><span></span><span></span><span></span></div>
  <p class="abs copy">Copyright © 2015 Saffron Lane<br>Privacy &amp; Policy .</p>
  <h3 class="abs tweets-title">Latest Tweets</h3>
  <p class="abs tweet"><span class="lead">sit amet, consectetur adipi-</span><br>sicing elit, sed do eiusmod tempor incididunt ut labore et dolore magna aliqua.<br><span class="time">10 minutes ago</span></p>
  <ul class="abs links" style="left:760px;top:2217px">
    <li>Home</li><li>About Us</li><li>Services</li><li>Products</li><li>Gallery</li><li>Contact Us</li>
  </ul>
  <ul class="abs links" style="left:945px;top:2217px">
    <li>My Account</li><li>Site Map</li><li>Gift Certificates</li><li>What is Saffron Lane</li><li>Saffron Lane</li>
  </ul>

</div>
</body>
</html>
```